Bramblewick Forage Business Cards

I need a business card with my logo, number, Facebook account, and some information about what I am selling. Green card with logo on the front. 555-214-8392 phone number, @bramblewickforage Facebook, •Orchardgrass Hay •Alfalfa Hay •Mixed Grass Hay , and “Premium Quality Hay” all written on the back.

Target Market(s)

Hay

Contact Information for Business Card

Phone number, Facebook, different types of hay.

Colors
00AB8E
00BBA5
67D7C9
C6EFE9
E9F9F6

```html
<!DOCTYPE html>
<html lang="en">
<head>
<meta charset="utf-8">
<title>Bramblewick Forage Business Cards</title>
<link rel="stylesheet" href="https://fonts.googleapis.com/css2?family=Arimo:wght@400;700&family=Yellowtail&display=swap">
<style>
  :root {
    --page-bg: #2b2b2b;
    --card-white: #ffffff;
    --brand-green: #00a651;
    --ink-dark: #2a2a2a;
    --ink-mid: #444444;
    --divider: #3a3a3a;
    --on-green: #ffffff;
  }
  * { margin: 0; padding: 0; box-sizing: border-box; }
  html, body {
    width: 1200px; height: 930px; overflow: hidden;
    background: var(--page-bg);
    font-family: "Arimo", Arial, sans-serif;
  }
  .canvas { position: relative; width: 1200px; height: 930px; }

  .card {
    position: absolute;
    border-radius: 21px;
    box-shadow: 0 6px 14px rgba(0,0,0,0.45);
  }
  .card--front { left: 279px; top: 74px; width: 639px; height: 364px; background: var(--card-white); }
  .card--back  { left: 277px; top: 490px; width: 641px; height: 366px; background: var(--brand-green); }

  .brand { position: absolute; display: flex; align-items: center; gap: 10px; }
  .brand__dot { border-radius: 50%; flex: none; }
  .brand__name { font-weight: 700; white-space: nowrap; }

  .card--front .brand { left: 55px; top: 158px; }
  .card--front .brand__dot { width: 30px; height: 30px; background: var(--brand-green); }
  .card--front .brand__name { font-size: 21px; color: var(--ink-dark); }

  .divider { position: absolute; left: 319px; top: 126px; width: 2px; height: 114px; background: var(--divider); }

  .contact { position: absolute; left: 344px; top: 124px; }
  .contact__name { font-family: "Yellowtail", cursive; font-size: 30px; color: var(--brand-green); line-height: 1; }
  .contact__role { font-size: 17px; color: var(--ink-dark); margin-top: 2px; letter-spacing: -0.3px; }
  .contact__list { list-style: none; margin-top: 22px; }
  .contact__item { display: flex; align-items: center; gap: 9px; font-size: 18px; color: var(--ink-mid); height: 26px; letter-spacing: -0.3px; }
  .contact__icon { width: 15px; height: 15px; flex: none; }
  .contact__square { width: 14px; height: 14px; background: var(--brand-green); border-radius: 2px; flex: none; }

  .card--back .brand { left: 0; right: 0; top: 150px; justify-content: center; gap: 14px; }
  .card--back .brand__dot { width: 40px; height: 40px; background: var(--on-green); }
  .card--back .brand__name { font-size: 32px; color: var(--on-green); }

  .products {
    position: absolute; left: 0; right: 0; top: 275px;
    display: flex; justify-content: center; gap: 14px;
    list-style: none; color: var(--on-green); font-weight: 700; font-size: 19px;
  }
  .products li::before { content: "\2022"; margin-right: 5px; }
  .tagline {
    position: absolute; left: 0; right: 0; top: 306px; text-align: center;
    font-family: "Yellowtail", cursive; font-size: 27px; color: var(--on-green);
  }
</style>
</head>
<body>
<main class="canvas">
  <section class="card card--front">
    <div class="brand">
      <span class="brand__dot"></span>
      <span class="brand__name">Bramblewick Forage</span>
    </div>
    <div class="divider"></div>
    <div class="contact">
      <p class="contact__name">Dana Whitlock</p>
      <p class="contact__role">Owner</p>
      <ul class="contact__list">
        <li class="contact__item">
          <svg class="contact__icon" viewBox="0 0 24 24" aria-hidden="true">
            <path fill="#00a651" d="M6.6 10.8a15.2 15.2 0 0 0 6.6 6.6l2.2-2.2c.3-.3.7-.4 1-.2 1.1.4 2.3.6 3.6.6.6 0 1 .4 1 1V20c0 .6-.4 1-1 1A17 17 0 0 1 3 4c0-.6.4-1 1-1h3.5c.6 0 1 .4 1 1 0 1.3.2 2.5.6 3.6.1.3 0 .7-.2 1z"/>
          </svg>
          555-214-8392
        </li>
        <li class="contact__item">
          <span class="contact__square"></span>
          @bramblewickforage
        </li>
      </ul>
    </div>
  </section>

  <section class="card card--back">
    <div class="brand">
      <span class="brand__dot"></span>
      <span class="brand__name">Bramblewick Forage</span>
    </div>
    <ul class="products">
      <li>Orchardgrass Hay</li>
      <li>Alfalfa Hay</li>
      <li>Mixed Grass Hay</li>
    </ul>
    <p class="tagline">Premium Quality Hay</p>
  </section>
</main>
</body>
</html>
```